Healthcare and Professional IT Services Company need a redesigned business card

We are a IT Services company that targets small medical practices and professional business such as Attorneys, Accounts, Architects etc. We want to communicate a professional yet friendly image using recent logo redesign here on ArtHarbor. Like to see the colors blue and orange in the design. Must use the Tall Pine Computing as displayed in the new logo - then also want to incorporate the fish logo as well.

Target Market(s)

Small medical and professional services

Industry/Entity Type

It Company

Contact Information for Business Card

The usual stuff, place for name address phone website. Also maybe our tagline which is "hooked on technology"

Requirements
Must have
• My new logo and the fish somewhere on the card

```html
<!DOCTYPE html>
<html lang="en">
<head>
<meta charset="utf-8">
<title>Tall Pine Computing — Business Card</title>
<link rel="stylesheet" href="https://fonts.googleapis.com/css2?family=Source+Sans+3:wght@400;600&display=swap">
<style>
  :root {
    --page-bg: #3a3a3a;
    --card-white: #f7f7f7;
    --brand-blue: #1b8fd8;
    --deep-blue: #1470b8;
    --accent-orange: #f18a1c;
    --ink: #3c3c3c;
    --white: #ffffff;
    --fish-tone: #6fb3e6;
    --fish-tone-light: #4a93d0;
  }
  * { margin: 0; padding: 0; box-sizing: border-box; }
  html, body {
    width: 1200px;
    height: 750px;
    overflow: hidden;
    background: var(--page-bg);
    font-family: "Source Sans 3", sans-serif;
  }
  .canvas { position: relative; width: 1200px; height: 750px; }
  .card {
    position: absolute;
    top: 228px;
    width: 461px;
    height: 262px;
    overflow: hidden;
  }
  .card--front { left: 124px; background: var(--card-white); }
  .card--back { left: 618px; background: var(--deep-blue); }

  .front-illustration {
    position: absolute;
    left: 308px; top: 22px;
    width: 120px; height: 82px;
    border-radius: 40px 44px 36px 30px;
    background: radial-gradient(circle at 60% 45%, #d6ebf9, #bcdcf3);
  }
  .brand-name {
    position: absolute;
    left: 282px; top: 112px;
    width: 160px;
    text-align: right;
    font-size: 24px;
    line-height: 24px;
    font-weight: 600;
    color: var(--brand-blue);
  }

  .person-name {
    position: absolute; left: 23px; top: 118px;
    font-size: 19px; font-weight: 600; color: var(--brand-blue);
  }
  .person-title {
    position: absolute; left: 23px; top: 141px;
    font-size: 12.5px; color: var(--accent-orange);
  }
  .address {
    position: absolute; left: 23px; top: 164px;
    font-size: 11px; line-height: 14px; color: var(--ink);
  }
  .contact-list { position: absolute; left: 23px; top: 196px; list-style: none; }
  .contact-item {
    display: flex; align-items: center;
    height: 18px;
    font-size: 11px; color: var(--ink);
  }
  .contact-icon { width: 12px; height: 12px; margin-right: 7px; fill: var(--brand-blue); }

  .back-illustration {
    position: absolute;
    left: 102px; top: 36px;
    width: 260px; height: 182px;
    border-radius: 90px 100px 80px 70px;
    background: radial-gradient(circle at 62% 45%, var(--fish-tone-light), var(--deep-blue) 75%);
  }
  .tagline {
    position: absolute; left: 0; right: 0; top: 229px;
    text-align: center;
    font-size: 12.5px; color: var(--white);
  }
</style>
</head>
<body>
<main class="canvas">
  <section class="card card--front">
    <div class="front-illustration" role="img" aria-label="Cartoon fish mascot illustration in blue outline"></div>
    <div class="brand-name">Tall Pine Computing</div>

    <h1 class="person-name">Adam Reyes</h1>
    <p class="person-title">CEO/Founder</p>
    <p class="address">4120 Birchwood Road<br>Juneau, Alaska 99801</p>

    <ul class="contact-list">
      <li class="contact-item">
        <svg class="contact-icon" viewBox="0 0 24 24"><path d="M6.6 10.8a15.1 15.1 0 0 0 6.6 6.6l2.2-2.2a1 1 0 0 1 1-.25 11.4 11.4 0 0 0 3.6.57 1 1 0 0 1 1 1V20a1 1 0 0 1-1 1A17 17 0 0 1 3 4a1 1 0 0 1 1-1h3.5a1 1 0 0 1 1 1c0 1.25.2 2.45.57 3.57a1 1 0 0 1-.25 1z"/></svg>
        555 214 7730
      </li>
      <li class="contact-item">
        <svg class="contact-icon" viewBox="0 0 24 24"><path d="M2 5h20v14H2z M2 5l10 8 10-8" fill="none" stroke="var(--brand-blue)" stroke-width="0"/><path d="M2 5h20v2l-10 7L2 7z"/><path d="M2 9l10 7 10-7v10H2z"/></svg>
        hello@tallpine.com
      </li>
      <li class="contact-item">
        <svg class="contact-icon" viewBox="0 0 24 24"><circle cx="12" cy="12" r="10"/><path d="M7 8c2 0 3 1 3 3s2 2 2 4-1 3-1 4M15 5c-1 2 0 3 2 3s2 2 1 3" fill="none" stroke="#fff" stroke-width="1.6"/></svg>
        www.tallpine.com
      </li>
    </ul>
  </section>

  <section class="card card--back">
    <div class="back-illustration" role="img" aria-label="Large white outline cartoon fish mascot"></div>
    <p class="tagline">Hooked on technology</p>
  </section>
</main>
</body>
</html>
```